Business Card for Coach - ready to print

Design Business Card ready to order prints www.lukasbrenner.coach

* An Overview / Background of the Business & Services
· Coaching
· Personal growth
* The Target Market / Audience you are trying to reach
· private person in different roles (self, familiy, business role)s
* Design Specifics; any preferences or ideas for Style, Colour, Imagery, etc
· See www.lukasbrenner.coach
· "simple" design
· (small) element of surprise / unusual element

* Information that will be placed in the Business Card
· Beratung und Coaching
· Address: Lukas Brenner, Mosering 42, CH-8312 Winterthur, Mobile +41 79 264 53 07
* Do you have an existing website or Facebook page where designers can learn more about your company?
· lukasbrenner.coach

Target Market(s)

private person in different roles (self, familiy, business role)

Industry/Entity Type

Life Coaching

Contact Information for Business Card

Lukas Brenner
Mosering 42
CH-8312 Winterthur

Mobile: +41 79 264 53 07
Email: lubr@alpimail.ch
www.lukasbrenner.coach

Font styles to use
Sans Serif

Colors

Designer to choose colors to be used in the design.

Requirements
Must have
• "simple" design
• element of surprise / unusual element
• Beratung & Coaching
• see www.lukasbrenner.coach for colors and so...
Nice to have
• TA Symbol (three rings on top of each other) - unsual presentation
• QR Code of Website (see if it fits in and still looks good).

```html
<!DOCTYPE html>
<html lang="de">
<head>
<meta charset="utf-8">
<title>Lukas Brenner – Visitenkarte</title>
<link href="https://fonts.googleapis.com/css2?family=Open+Sans:wght@400;600;700&display=swap" rel="stylesheet">
<style>
  :root {
    --backdrop: #9b9b9b;
    --brand-blue: #028cb5;
    --brand-blue-light: #3aa9cb;
    --brand-blue-dark: #016f90;
    --card-white: #ffffff;
    --tagline-white: #d9f0f7;
    --text-grey: #444444;
  }
  html, body {
    margin: 0;
    padding: 0;
    width: 1133px;
    height: 1200px;
    overflow: hidden;
    background: var(--backdrop);
    font-family: "Open Sans", sans-serif;
  }
  .canvas {
    position: relative;
    width: 1133px;
    height: 1200px;
  }
  .card {
    position: absolute;
    left: 219px;
    width: 694px;
    height: 396px;
    overflow: hidden;
  }
  .card--front {
    top: 153px;
    background: var(--brand-blue);
    display: flex;
    flex-direction: column;
    align-items: center;
    justify-content: center;
  }
  .front-name {
    margin: 0;
    color: var(--card-white);
    font-weight: 700;
    font-size: 58px;
    line-height: 64px;
    letter-spacing: 0.5px;
  }
  .front-tagline {
    margin: 10px 0 0;
    color: var(--tagline-white);
    font-weight: 600;
    font-size: 17px;
    letter-spacing: 5px;
    text-transform: uppercase;
  }
  .page-turn {
    position: absolute;
    right: 0;
    bottom: 0;
    width: 64px;
    height: 64px;
  }
  .card--back {
    top: 649px;
    background: var(--card-white);
  }
  .identity {
    position: absolute;
    right: 397px;
    top: 160px;
    text-align: right;
    color: var(--text-grey);
  }
  .identity__name {
    margin: 0 0 2px;
    color: var(--brand-blue);
    font-weight: 700;
    font-size: 27px;
    line-height: 32px;
  }
  .identity__address {
    margin: 0;
    font-size: 19px;
    line-height: 25px;
  }
  .divider {
    position: absolute;
    left: 325px;
    top: 164px;
    width: 2px;
    height: 76px;
    background: var(--brand-blue);
  }
  .contacts {
    position: absolute;
    left: 346px;
    top: 160px;
    margin: 0;
    padding: 0;
    list-style: none;
    color: var(--text-grey);
    font-size: 19.5px;
    line-height: 28px;
  }
  .contacts li {
    display: flex;
    align-items: center;
    gap: 5px;
  }
  .contacts svg {
    width: 15px;
    height: 15px;
    fill: var(--brand-blue);
    flex: none;
  }
</style>
</head>
<body>
<main class="canvas">
  <section class="card card--front">
    <h1 class="front-name">LUKAS BRENNER</h1>
    <p class="front-tagline">Beratung &amp; Coaching</p>
    <svg class="page-turn" viewBox="0 0 64 64" aria-hidden="true">
      <polygon points="64,0 64,64 0,64" fill="var(--backdrop)"/>
      <polygon points="64,0 0,64 0,0" fill="var(--brand-blue-light)"/>
      <line x1="64" y1="0" x2="0" y2="64" stroke="var(--brand-blue-dark)" stroke-width="1"/>
    </svg>
  </section>

  <section class="card card--back">
    <div class="identity">
      <h2 class="identity__name">LUKAS BRENNER</h2>
      <p class="identity__address">Mosering 42<br>CH-8312 Winterthur</p>
    </div>
    <div class="divider"></div>
    <ul class="contacts">
      <li>
        <svg viewBox="0 0 16 16" aria-hidden="true"><path d="M3.6 1.2l2.2 2.6-1.3 1.8c.9 2 2.5 3.6 4.5 4.6l1.8-1.3 2.6 2.2-1.4 2.3C6.7 13.7 2.3 9.3 1.6 2.6z"/><path d="M9.5 2a5 5 0 0 1 4.5 4.5h-1.3A3.7 3.7 0 0 0 9.5 3.3zM9.5 4.6a2.4 2.4 0 0 1 1.9 1.9h-1.3a1.2 1.2 0 0 0-.6-.6z"/></svg>
        <span>+41 79 264 53 07</span>
      </li>
      <li>
        <svg viewBox="0 0 16 16" aria-hidden="true"><path d="M1.5 4h13v1.2L8 9 1.5 5.2z"/><path d="M1.5 6.6L8 10.4l6.5-3.8V12.5h-13z"/></svg>
        <span>lubr@alpimail.ch</span>
      </li>
      <li>
        <svg viewBox="0 0 16 16" aria-hidden="true"><circle cx="8" cy="8" r="7"/><path fill="#fff" d="M4 4.5c1.5-.6 2.8 0 3 1.2.2 1-1 1.3-1.2 2.3-.2 1 .8 1.7.4 2.7-.8-.2-1.9-1.6-2.2-3-.2-1.1-.6-2.2 0-3.2zM9.5 9.5c.9-.4 2 .1 2.1 1-.3 1-1.3 1.8-2.4 2.1-.3-.8-.4-2.4.3-3.1z"/></svg>
        <span>www.lukasbrenner.coach</span>
      </li>
    </ul>
  </section>
</main>
</body>
</html>
```